Bookcover: Ways to Turn Into a Bold Pathfinder

I am publishing a super-low-cost innovation book for €4,99 on Quillmere Open Press to help everyone become a great innovator: young ambitious people without college education nor a big budget. Do you want to help me?

Brief:
Design a book cover 1600 x 2560 pixels for QOP.
Main title: Ways to Turn Into a Bold Pathfinder
Sub title: mindset - insights - skills & tools
Author: Joost ter Brakel
Design: captive, and appealing to everyone
Target Group: young ambitious people without college education

For quillmere please format the height/width ratio of 1.6:1

```html
<!DOCTYPE html>
<html lang="en">
<head>
<meta charset="utf-8">
<title>Ways to Turn Into a Bold Pathfinder — Book Cover</title>
<link rel="stylesheet" href="https://fonts.googleapis.com/css2?family=Montserrat:wght@400;500;700;800&display=swap">
<style>
  :root {
    --page-bg: #ffffff;
    --cover-bg: #05060b;
    --title-orange: #f7941d;
    --title-white: #ffffff;
    --rule-orange: #c8761a;
    --glow-core: #c9dcff;
    --glow-mid: #3a5fb0;
    --glow-deep: #16254f;
  }
  * { margin: 0; padding: 0; box-sizing: border-box; }
  html, body {
    width: 1200px;
    height: 1200px;
    overflow: hidden;
    background: var(--page-bg);
  }
  .book-cover {
    position: absolute;
    left: 240px;
    top: 24px;
    width: 720px;
    height: 1152px;
    background: var(--cover-bg);
    overflow: hidden;
    font-family: "Montserrat", Arial, sans-serif;
    color: var(--title-white);
  }
  .cover-art {
    position: absolute;
    left: 0;
    top: 410px;
    width: 720px;
    height: 620px;
    background:
      radial-gradient(ellipse 190px 160px at 424px 210px, var(--glow-core) 0%, rgba(150,180,240,0.55) 40%, rgba(58,95,176,0) 100%),
      radial-gradient(ellipse 430px 330px at 400px 250px, var(--glow-mid) 0%, var(--glow-deep) 55%, rgba(5,6,11,0) 100%);
  }
  .cover-title { font-weight: inherit; font-size: inherit; }
  .title-lead,
  .title-main {
    position: absolute;
    left: 0;
    width: 100%;
    text-align: center;
    line-height: 1;
    white-space: nowrap;
  }
  .title-lead {
    top: 84px;
    color: var(--title-orange);
    font-weight: 500;
    font-size: 50px;
    letter-spacing: 0.5px;
  }
  .title-main {
    font-weight: 700;
    letter-spacing: -2px;
  }
  .title-main.line-one { top: 140px; font-size: 103px; }
  .title-main.line-two { top: 247px; font-size: 90px; }
  .subtitle {
    position: absolute;
    left: 130px;
    top: 355px;
    width: 460px;
    height: 40px;
    border-top: 1px solid var(--rule-orange);
    border-bottom: 1px solid var(--rule-orange);
    display: flex;
    align-items: center;
    justify-content: center;
    font-weight: 400;
    font-size: 27px;
    line-height: 1;
    letter-spacing: 0.6px;
    white-space: nowrap;
  }
  .author {
    position: absolute;
    top: 1057px;
    width: 100%;
    text-align: center;
    font-weight: 700;
    font-size: 56px;
    line-height: 1;
  }
</style>
</head>
<body>
  <main class="book-cover">
    <div class="cover-art" role="img" aria-label="Photo of an open hand holding up a glowing brain crackling with electric lightning on a dark blue background"></div>
    <h1 class="cover-title">
      <span class="title-lead">Ways to Turn Into a</span>
      <span class="title-main line-one">BOLD</span>
      <span class="title-main line-two">PATHFINDER</span>
    </h1>
    <p class="subtitle">mindset - insights - skills &amp; tools</p>
    <p class="author">Joost ter Brakel</p>
  </main>
</body>
</html>
```